Talents and colours poster for home office

The objective is to illustrate/communicate and remember 5 talents and 4 colours of the personality.

The infographic will be hanged on the wall of an home office. It need to be simple and clear. Illustrations and pictograms can be used. It can be artistic.

Here's the content:

5 talents,scaling in priority from #1 to #5
Ideation / creativity
Winning other over / charisma
Adaptability
Positivity
Empathy

In the files there is a description of what those mean.

You have to include 4 colours, scaling in priority from #1 to #4
Yellow
Green
Red
Blue

I made a sketch just for fun... and to show why I need professionnal skills :)

THX

Industry/Entity Type

Office

Requirements
Should not have
• offensive materials

```html
<!DOCTYPE html>
<html lang="en">
<head>
<meta charset="utf-8">
<title>Talents and Colours</title>
<link rel="stylesheet" href="https://fonts.googleapis.com/css2?family=Cinzel:wght@500&display=swap">
<style>
  :root {
    --yellow: #f7e600;
    --yellow-light: #fbeb2a;
    --green: #2fa56b;
    --green-light: #8cc98e;
    --red: #e1261f;
    --red-light: #ee3a2c;
    --blue: #1f56b0;
    --blue-light: #2f6ac0;
    --label: #ffffff;
    --label-shadow: rgba(40, 30, 20, 0.75);
  }
  html, body {
    margin: 0;
    padding: 0;
    overflow: hidden;
    background: #ffffff;
  }
  .poster {
    position: relative;
    width: 848px;
    height: 1200px;
    overflow: hidden;
    font-family: "Cinzel", "Copperplate", serif;
  }
  .band {
    position: absolute;
    left: 0;
    width: 848px;
    height: 300px;
  }
  .band--yellow {
    top: 0;
    background: radial-gradient(ellipse at 30% 40%, var(--yellow-light), var(--yellow) 70%);
  }
  .band--green {
    top: 300px;
    background: linear-gradient(90deg, var(--green) 0%, #3fae70 50%, var(--green-light) 100%);
  }
  .band--red {
    top: 600px;
    background: radial-gradient(ellipse at 60% 50%, var(--red-light), var(--red) 75%);
  }
  .band--blue {
    top: 900px;
    background: linear-gradient(160deg, var(--blue-light) 0%, var(--blue) 60%, #243f9a 100%);
  }
  .portrait-area {
    position: absolute;
    left: 70px;
    top: 250px;
    width: 708px;
    height: 650px;
    background: radial-gradient(ellipse 50% 55% at 50% 50%,
      rgba(20, 30, 30, 0.30) 0%,
      rgba(20, 30, 30, 0.22) 45%,
      rgba(20, 30, 30, 0) 100%);
  }
  .talent {
    position: absolute;
    left: 0;
    width: 848px;
    margin: 0;
    text-align: center;
    color: var(--label);
    font-size: 36px;
    font-weight: 500;
    letter-spacing: 1.7px;
    line-height: 1;
    text-shadow: 2px 2px 2px var(--label-shadow);
    white-space: nowrap;
  }
  .talent--1 { top: 133px; }
  .talent--2 { top: 358px; }
  .talent--3 { top: 582px; }
  .talent--4 { top: 807px; }
  .talent--5 { top: 1032px; }
</style>
</head>
<body>
  <main class="poster">
    <div class="band band--yellow"></div>
    <div class="band band--green"></div>
    <div class="band band--red"></div>
    <div class="band band--blue"></div>

    <div class="portrait-area" role="img" aria-label="Illustration of a calm human head and shoulders, tinted by the colour bands"></div>

    <h2 class="talent talent--1">IDEATION / CREATIVITY</h2>
    <h2 class="talent talent--2">WINNING OTHER OVER / CHARISMA</h2>
    <h2 class="talent talent--3">ADAPTABILITY</h2>
    <h2 class="talent talent--4">POSITIVITY</h2>
    <h2 class="talent talent--5">EMPATHY</h2>
  </main>
</body>
</html>
```